Business Card for Polygraph business in Africa

Business Card . Polygraph Examiner based in Tanzania, East Africa.
Business Card will be used to disseminate contact information to potential clients.
It should convey that I am a professional specifically in the polygraph field and perform my work with integrity.

I have attached the business card that I'm currently using, which I threw together myself initially. It's not professional enough.

Target Market(s)

Banks, Accounting Firms, Government Ministries, Gas, Oil, & Gemstone Mining Concerns, Wildlife Conservation NGOs, International companies located in East Africa.

Industry/Entity Type

Business

Contact Information for Business Card

Veritrace Kilonga
Miriam Holloway
PO Box 48317
Arusha, Tanzania
+255 612 839 274
miriamholloway@postvale.example

Colors
00a990
f37122
faa54b

Requirements
Must have
• - Veritrace Kilonga (with the word "Polygraph" being more prominent than the word "Tanzania")
• - Forensic Examinations
• - Employment Screening
• - Should contain a logo of the Continental Truthline Society (of which I'm a member)
• - I would like an accent design (such as the polygraph "squiggles" of a cardio tracing or such as that)
• - My contact information (less prominent, but large enough to read legibly). I would also consider putting the contact information on the second side of the card.
Nice to have
• My color suggestions are changeable.
Should not have
• Anything "cutesy" or "cartoonish"

```html
<!DOCTYPE html>
<html lang="en">
<head>
<meta charset="utf-8">
<title>Veritrace Kilonga – Business Card</title>
<link rel="stylesheet" href="https://fonts.googleapis.com/css2?family=Roboto:wght@400;500;700&family=Roboto+Condensed:wght@500&display=swap">
<style>
  :root{
    --brand-blue:#044592;
    --card-white:#f3f3f3;
    --ring-grey:#5d5d5d;
    --text-light:#ffffff;
    --backdrop:#e6e6e6;
  }
  *{margin:0;padding:0;box-sizing:border-box}
  html,body{width:1200px;height:960px;overflow:hidden;background:var(--backdrop)}
  .canvas{position:relative;width:1200px;height:960px}
  .card{position:absolute;width:600px;height:343px;overflow:hidden;font-family:"Roboto",sans-serif}
  .card--front{left:314px;top:113px;background:var(--brand-blue)}
  .card--back{left:312px;top:472px;background:var(--brand-blue)}
  .front-shape{position:absolute;inset:0}
  .holder{position:absolute;left:38px;top:44px;color:var(--text-light)}
  .holder__name{font-family:"Roboto Condensed",sans-serif;font-weight:500;font-size:21px;letter-spacing:.2px}
  .holder__company{font-size:15px;font-weight:500;margin-top:3px;letter-spacing:.3px}
  .address{position:absolute;left:38px;top:199px;color:var(--text-light);font-size:13px;line-height:19px}
  .contact{position:absolute;left:38px;top:248px;list-style:none;color:var(--text-light);font-size:13px;line-height:19.5px}
  .contact li{display:flex;align-items:center;gap:7px;white-space:nowrap}
  .contact svg{width:14px;height:14px;flex:none}
  .brand-mark{position:absolute;left:310px;top:148px;display:flex;align-items:center;gap:10px;color:var(--brand-blue);font-weight:700;font-size:27px}
  .brand-mark__dot{width:22px;height:22px;border-radius:50%;background:var(--brand-blue)}
  .member-badge{position:absolute;left:505px;top:15px;width:76px;height:76px;border-radius:50%;background:var(--card-white);border:3px solid var(--brand-blue)}
  .back-name{position:absolute;left:0;right:0;top:152px;text-align:center;color:var(--text-light);font-weight:700;font-size:34px}
  .services{position:absolute;left:0;right:0;top:288px;text-align:center;color:var(--text-light);font-size:15px}
  .services__sep{display:inline-block;width:6px;height:6px;border-radius:50%;background:var(--text-light);margin:0 8px 2px}
</style>
</head>
<body>
<main class="canvas">
  <section class="card card--front">
    <svg class="front-shape" viewBox="0 0 600 343" width="600" height="343">
      <circle cx="462" cy="177" r="217" fill="var(--ring-grey)"/>
      <circle cx="462" cy="177" r="209" fill="var(--card-white)"/>
    </svg>
    <div class="holder">
      <p class="holder__name">MIRIAM HOLLOWAY</p>
      <p class="holder__company">VERITRACE KILONGA</p>
    </div>
    <p class="address">PO Box 48317<br>Arusha, Tanzania</p>
    <ul class="contact">
      <li><svg viewBox="0 0 24 24"><path fill="#fff" d="M6.6 10.8a15 15 0 0 0 6.6 6.6l2.2-2.2c.3-.3.7-.4 1-.2 1.1.4 2.3.6 3.6.6.6 0 1 .4 1 1V20c0 .6-.4 1-1 1A17 17 0 0 1 3 4c0-.6.4-1 1-1h3.5c.6 0 1 .4 1 1 0 1.3.2 2.5.6 3.6.1.3 0 .7-.2 1z"/></svg>+255 612 839 274</li>
      <li><svg viewBox="0 0 24 24"><path fill="#fff" d="M2 6h20v12H2z"/><path fill="none" stroke="#044592" stroke-width="2" d="M2 6l10 7 10-7"/></svg>miriamholloway@postvale.example</li>
      <li><svg viewBox="0 0 24 24"><circle cx="12" cy="12" r="10" fill="#fff"/><path fill="#044592" d="M8 7c2 1 3 3 2 5s-3 1-3 4c-2-2-3-5-1-8zm7 3c2 0 3 2 2 4s-2 3-4 3c0-2 0-3 1-4s0-3 1-3z"/></svg>www.miriamholloway.example</li>
    </ul>
    <div class="brand-mark"><span class="brand-mark__dot"></span>Veritrace Kilonga</div>
    <div class="member-badge" role="img" aria-label="Continental Truthline Society membership badge"></div>
  </section>

  <section class="card card--back">
    <p class="back-name">Veritrace Kilonga</p>
    <p class="services">Forensic Examinations<span class="services__sep"></span>Employment Screening</p>
  </section>
</main>
</body>
</html>
```